Specialised investor in e-mobility and energy wants business card design

We need a business card design that fits our existing corporate design. <The look and feel must be 'sharp'/'clean', dynamic, communicate momentum, professionalism etc (as one would imagine from a firm in the financial sector). We like the idea of a reverse-side of the card that includes the logo, and the name and contact details on the other. We expect the deliverable to be whatever format might be required to be able to get cards printed directly by a service such as kelmo press. Our website is www.zub.capital

```html
<!DOCTYPE html>
<html lang="en">
<head>
<meta charset="utf-8">
<title>Zub Capital – Business Card</title>
<link href="https://fonts.googleapis.com/css2?family=Poppins:wght@300;400;600;700&display=swap" rel="stylesheet">
<style>
  :root {
    --backdrop: #b7b7b7;
    --green-dark: #2e4d21;
    --green-mid: #5a8a36;
    --green-light: #89b34b;
    --white: #ffffff;
    --rule: rgba(255,255,255,0.55);
  }
  html, body {
    margin: 0;
    padding: 0;
    width: 1200px;
    height: 1200px;
    overflow: hidden;
    background: var(--backdrop);
    font-family: "Poppins", sans-serif;
  }
  .stage {
    position: relative;
    width: 1200px;
    height: 1200px;
  }
  .card {
    position: absolute;
    top: 305px;
    width: 370px;
    height: 597px;
    box-shadow: 4px 4px 4px rgba(0,0,0,0.45);
    overflow: hidden;
  }
  .card-front {
    left: 202px;
    background: linear-gradient(30deg, var(--green-dark) 15%, #4f7a31 50%, var(--green-light) 100%);
  }
  .card-back {
    left: 603px;
    width: 366px;
    background: var(--white);
  }
  .wordmark {
    position: absolute;
    left: 0;
    right: 0;
    text-align: center;
    font-weight: 400;
    letter-spacing: 0.5px;
    white-space: nowrap;
  }
  .card-front .wordmark {
    top: 500px;
    font-size: 44px;
    color: var(--white);
  }
  .card-back .wordmark {
    top: 98px;
    font-size: 40px;
    color: var(--green-dark);
  }
  .wave {
    position: absolute;
    left: 0;
    top: 0;
    width: 366px;
    height: 597px;
  }
  .details {
    position: absolute;
    left: 0;
    right: 0;
    text-align: center;
    color: var(--white);
    white-space: nowrap;
  }
  .person-name {
    top: 340px;
    font-size: 25px;
    line-height: 1;
    color: var(--green-light);
    letter-spacing: 0.3px;
  }
  .person-name .given { font-weight: 700; }
  .person-name .family { font-weight: 300; }
  .person-title {
    top: 366px;
    font-size: 17px;
    font-weight: 400;
  }
  .icon-row {
    position: absolute;
    top: 401px;
    left: 0;
    right: 0;
    display: flex;
    justify-content: center;
    align-items: center;
    gap: 4px;
  }
  .icon-row .rule {
    width: 52px;
    height: 1px;
    background: var(--rule);
    margin: 0 4px;
  }
  .icon {
    width: 25px;
    height: 25px;
    border-radius: 3px;
    background: var(--green-light);
    display: flex;
    align-items: center;
    justify-content: center;
  }
  .contact {
    top: 433px;
    font-size: 17px;
    line-height: 21px;
    font-weight: 400;
  }
  .divider {
    position: absolute;
    top: 512px;
    left: 89px;
    width: 195px;
    height: 1px;
    background: var(--rule);
  }
  .address {
    top: 523px;
    font-size: 17px;
    line-height: 21px;
    font-weight: 400;
  }
</style>
</head>
<body>
<div class="stage">

  <section class="card card-front">
    <div class="wordmark">Zub Capital</div>
  </section>

  <section class="card card-back">
    <div class="wordmark">Zub Capital</div>

    <svg class="wave" viewBox="0 0 366 597" aria-hidden="true">
      <path d="M0 276 C40 250 100 246 160 252 C240 262 310 295 366 332 L366 354 C300 310 230 270 150 258 C90 252 40 262 0 285 Z" fill="#89b34b"/>
      <path d="M0 276 C40 254 110 248 170 258 C250 272 315 314 366 354 L366 597 L0 597 Z" fill="#2e4d21"/>
    </svg>

    <div class="details person-name"><span class="given">MARTEN</span> <span class="family">HOLLOWAY</span></div>
    <div class="details person-title">Managing Director</div>

    <div class="icon-row">
      <span class="rule"></span>
      <span class="icon" aria-label="Phone">
        <svg width="15" height="15" viewBox="0 0 16 16"><path d="M2 6c0-2 3-3 6-3s6 1 6 3v1h-3V6H5v1H2z M4 8h8l1 5H3z" fill="#fff"/></svg>
      </span>
      <span class="icon" aria-label="Email">
        <svg width="15" height="15" viewBox="0 0 16 16"><rect x="1.5" y="3.5" width="13" height="9" fill="none" stroke="#fff"/><path d="M1.5 3.5 8 9l6.5-5.5M1.5 12.5 6 7.5M14.5 12.5 10 7.5" fill="none" stroke="#fff"/></svg>
      </span>
      <span class="icon" aria-label="Website">
        <svg width="15" height="15" viewBox="0 0 16 16"><circle cx="8" cy="8" r="6.5" fill="#fff"/><path d="M5 4c2 1 1 3 3 3s1 3 3 4" fill="none" stroke="#89b34b" stroke-width="1.5"/></svg>
      </span>
      <span class="rule"></span>
    </div>

    <div class="details contact">
      044-318 702 564<br>
      info@zub.capital<br>
      www.zub.capital
    </div>

    <div class="divider"></div>

    <div class="details address">
      87, Harbour Lane, Suite 4<br>
      30217, Netherlands
    </div>
  </section>

</div>
</body>
</html>
```